Velvet Dice Night Age Verification Landing Page

To create a visually appealing design for the landing page of the adult game "Velvet Dice Night" that confirms the visitor's age.
The design should have a simple and visually appealing look that focuses on two buttons labeled "Yes" and "No". The purpose of the page is to confirm that the visitor is 18 years of age or older before accessing the game's content. Responsive design that works well on desktop and mobile devices. The final output should be delivered in PSD, AI, or Sketch format, along with any necessary images or assets.
I have also attached examples.

```html
<!DOCTYPE html>
<html lang="en">
<head>
<meta charset="utf-8">
<title>Velvet Dice Night – Age Verification</title>
<link rel="stylesheet" href="https://fonts.googleapis.com/css2?family=Dancing+Script:wght@500&family=Nunito:wght@400;700;800&display=swap">
<style>
  :root {
    --bg-dark: #070507;
    --bg-mid: #1c1519;
    --heart-top: #150f14;
    --heart-bottom: #8c5c98;
    --heart-fill: #ffffff;
    --heart-line: #2a1f2a;
    --accent: #9b58a6;
    --button: #83629a;
    --button-text: #ffffff;
    --body-text: #2b2230;
  }
  * { box-sizing: border-box; margin: 0; padding: 0; }
  html, body { width: 1200px; height: 720px; overflow: hidden; background: var(--bg-dark); }
  .page {
    position: relative;
    width: 1200px;
    height: 720px;
    overflow: hidden;
    font-family: "Nunito", sans-serif;
  }
  .hero-backdrop {
    position: absolute;
    inset: 0;
    background:
      radial-gradient(ellipse 45% 55% at 40% 45%, #2a2024 0%, rgba(20,15,18,0) 70%),
      radial-gradient(ellipse 30% 40% at 80% 55%, #241b20 0%, rgba(20,15,18,0) 70%),
      linear-gradient(180deg, var(--bg-mid) 0%, var(--bg-dark) 100%);
  }
  .brand {
    position: absolute;
    top: 82px;
    left: 0;
    width: 1200px;
    display: flex;
    justify-content: center;
    align-items: center;
    gap: 12px;
  }
  .brand-dot {
    width: 22px;
    height: 22px;
    border-radius: 50%;
    background: var(--accent);
  }
  .brand-name {
    font-family: "Nunito", sans-serif;
    font-weight: 800;
    font-size: 30px;
    color: var(--accent);
    letter-spacing: 0.5px;
  }
  .heart-frame {
    position: absolute;
    inset: 0;
    width: 1200px;
    height: 720px;
  }
  .age-gate {
    position: absolute;
    left: 0;
    width: 1200px;
    text-align: center;
  }
  .age-question {
    top: 322px;
    font-family: "Dancing Script", cursive;
    font-weight: 500;
    font-size: 38px;
    color: var(--accent);
  }
  .age-actions {
    top: 413px;
    display: flex;
    justify-content: center;
    gap: 13px;
  }
  .age-button {
    width: 93px;
    height: 40px;
    border: none;
    border-radius: 20px;
    background: var(--button);
    color: var(--button-text);
    font-family: "Nunito", sans-serif;
    font-weight: 800;
    font-size: 18px;
    letter-spacing: 0.5px;
  }
  .remember {
    top: 505px;
    display: flex;
    justify-content: center;
    align-items: center;
    gap: 12px;
    font-size: 14.5px;
    color: var(--body-text);
  }
  .remember-box {
    width: 19px;
    height: 19px;
    border: 1px solid var(--button);
    border-radius: 4px;
    background: #fff;
  }
</style>
</head>
<body>
<main class="page">
  <div class="hero-backdrop" role="img" aria-label="Dimly lit photo of a woman lying on a bed, dark moody background"></div>

  <header class="brand">
    <span class="brand-dot"></span>
    <span class="brand-name">Velvet Dice Night</span>
  </header>

  <svg class="heart-frame" viewBox="0 0 1500 900" aria-hidden="true">
    <defs>
      <linearGradient id="heartRim" x1="0" y1="0" x2="0" y2="1">
        <stop offset="0" stop-color="var(--heart-top)"/>
        <stop offset="0.45" stop-color="#3a2a3d"/>
        <stop offset="1" stop-color="var(--heart-bottom)"/>
      </linearGradient>
    </defs>
    <path fill="url(#heartRim)" d="M757,345 C700,270 645,240 590,240 C480,240 408,330 408,440 C408,520 450,570 520,640 L720,800 Q757,830 794,800 L990,640 C1060,570 1092,520 1092,440 C1092,330 1020,237 910,237 C860,237 810,270 757,345 Z"/>
    <path fill="var(--heart-fill)" d="M757,360 C702,290 648,258 592,258 C494,258 426,340 426,440 C426,512 464,560 532,628 L726,782 Q757,805 788,782 L980,628 C1046,560 1074,512 1074,440 C1074,340 1010,255 910,255 C862,255 812,288 757,360 Z"/>
    <path fill="none" stroke="var(--heart-line)" stroke-width="1" d="M757,357 C704,300 650,278 594,278 C506,278 440,350 440,440 C440,506 476,552 540,618 L730,772 Q757,794 784,772 L972,618 C1034,552 1060,506 1060,440 C1060,350 1002,273 910,273 C864,273 815,300 757,357 Z"/>
  </svg>

  <h1 class="age-gate age-question">Are you over 18 years of age?</h1>

  <div class="age-gate age-actions">
    <button class="age-button" type="button">YES</button>
    <button class="age-button" type="button">NO</button>
  </div>

  <label class="age-gate remember">
    <span class="remember-box"></span>
    <span class="remember-label">Remember me</span>
  </label>
</main>
</body>
</html>
```